Business Cards for new orthopaedic surgery practice

My husband and I are starting our own orthopaedic surgery practice. We are looking for a business card that is uniform, but one will have my name/title and the other will have his. You can just create one design with my name on it for now. But when I choose your design as the winning design I will ask that you add another copy with his name/title.

We are looking for classy, simple, elite all in one. We like dark blues/a little gold/yellow. Something that goes with our logo. We want our logo incorporated. Here is all the info you need:
Business name: RV Bone & Vitality Center
Location: 38517 North Willowmere Ave
Brindle Harbor, FL 34990
Phone: 954-218-4063
Fax: 954-582-7341
Email: info@myrvbonecare.example

Names: Lydia Vance, M.D.
Board Certified Hand and Upper Extremity Surgeon

Ebo Dansu, M.D.
Board Certified Hip & Knee Replacement/General Orthopaedic Surgeon

Can decide what you want to put on the back. Maybe a slogan:
Grounded in Skill. Centered on You

I am just going to upload our logo. The only thing is if we select you as the winning design, the location, and phone numbers may change. We will need your help to update that once fully solidified.

Industry/Entity Type

Medical

Contact Information for Business Card

Colors
0054AA
0677BA
7BADD7
CADEEF
E8F1F8
0094D4
00A9DD
6FCCEA
C7EBF8
E9F6FB

Requirements
Must have
• class, appeal,
Should not have
• We want to air on the side of masculine if we are looking at masculine vs. feminine feel. But we still want it classy, sophisticated, and something we will love

```html
<!DOCTYPE html>
<html lang="en">
<head>
<meta charset="utf-8">
<title>RV Bone &amp; Vitality Center — Business Cards</title>
<link rel="stylesheet" href="https://fonts.googleapis.com/css2?family=Montserrat:wght@400;500;600&display=swap">
<style>
  :root {
    --backdrop: #3a3a3c;
    --navy: #1b2a50;
    --gold: #c9a14e;
    --white: #ffffff;
    --ink-soft: #e6eaf3;
  }
  * { box-sizing: border-box; margin: 0; padding: 0; }
  html, body { width: 1200px; height: 875px; overflow: hidden; }
  body {
    background: var(--backdrop);
    font-family: "Montserrat", Arial, sans-serif;
    position: relative;
  }
  .card {
    position: absolute;
    width: 540px;
    height: 309px;
    background: var(--navy);
    border-radius: 18px;
    overflow: hidden;
    color: var(--white);
  }
  .card--front { left: 40px; top: 283px; }
  .card--back { left: 620px; top: 283px; }

  .brand {
    display: flex;
    align-items: center;
    gap: 10px;
    font-weight: 600;
    color: var(--white);
    letter-spacing: 0.04em;
    white-space: nowrap;
  }
  .brand__dot {
    flex: none;
    border: 2px solid var(--gold);
    border-radius: 50%;
  }

  .card--front .brand {
    position: absolute;
    left: 0; right: 0; top: 100px;
    justify-content: center;
    font-size: 20px;
  }
  .card--front .brand__dot { width: 22px; height: 22px; }
  .tagline {
    position: absolute;
    left: 0; right: 0; top: 196px;
    text-align: center;
    font-size: 15px;
    font-weight: 400;
    letter-spacing: 0.02em;
  }

  .card--back .brand {
    position: absolute;
    left: 34px; top: 36px;
    font-size: 13px;
  }
  .card--back .brand__dot { width: 16px; height: 16px; }
  .details { position: absolute; left: 34px; top: 110px; right: 34px; }
  .person__name {
    color: var(--gold);
    font-weight: 600;
    font-size: 20px;
    line-height: 1.1;
  }
  .person__title { font-size: 11.5px; margin-top: 3px; color: var(--ink-soft); }
  .address { font-size: 11.5px; line-height: 1.4; margin-top: 16px; }
  .contact { list-style: none; margin-top: 14px; font-size: 11.5px; line-height: 1.55; }
  .contact li { display: flex; align-items: center; gap: 8px; }
  .contact svg { width: 11px; height: 11px; fill: var(--gold); flex: none; }
</style>
</head>
<body>
  <section class="card card--front">
    <div class="brand"><span class="brand__dot"></span>RV Bone &amp; Vitality Center</div>
    <p class="tagline">Grounded in Skill. Centered on You</p>
  </section>

  <section class="card card--back">
    <div class="brand"><span class="brand__dot"></span>RV Bone &amp; Vitality Center</div>
    <div class="details">
      <p class="person__name">Lydia Vance, M.D.</p>
      <p class="person__title">Board Certified Hand and Upper Extremity Surgeon</p>
      <p class="address">38517 North Willowmere Ave<br>Brindle Harbor, FL 34990</p>
      <ul class="contact">
        <li><svg viewBox="0 0 24 24" aria-hidden="true"><path d="M6.6 10.8a15 15 0 0 0 6.6 6.6l2.2-2.2a1 1 0 0 1 1-.25 11.4 11.4 0 0 0 3.6.57 1 1 0 0 1 1 1V20a1 1 0 0 1-1 1A17 17 0 0 1 3 4a1 1 0 0 1 1-1h3.5a1 1 0 0 1 1 1c0 1.25.2 2.45.57 3.57a1 1 0 0 1-.25 1z"/></svg>954-218-4063</li>
        <li><svg viewBox="0 0 24 24" aria-hidden="true"><path d="M6 2h12v6H6zM4 9h16a2 2 0 0 1 2 2v6h-4v5H6v-5H2v-6a2 2 0 0 1 2-2zm4 8v3h8v-3z"/></svg>954-582-7341</li>
        <li><svg viewBox="0 0 24 24" aria-hidden="true"><path d="M2 5h20v14H2zm2 2v.5l8 5 8-5V7zm0 2.9V17h16V9.9l-8 5z"/></svg>info@myrvbonecare.example</li>
      </ul>
    </div>
  </section>
</body>
</html>
```